life insurance quote website design for lepontdoriole.ca

the web site lepontdoriole.ca need a design. we dont like the actuel one but we are open at all new suggestion. visit us at lepontdoriole.ca and you will understand. the principal concurant is tarifsgarantisnord.ca, calculeo.ca, coutprotecfam.ca. We are a life insurance quote site. we found best price available in the canadien industrie. We absolutly want a design with our form in the front page on the top right side like our concurance, we use wordpress at this time. we want to be able to switch language. and to have a logic form. we want to be able to change the color for each type of insurance quote page.we also need a blog in it to post news. and the site will be SEO accurate.

Target Market(s)

Get client fill the quote form

Industry/Entity Type

Insurance

Number of Pages Required

3 page

Font styles to use
Sans Serif

Requirements
Must have
• logic form on the top right first page
• page template for product info stuff, contact, and who we are, blog
• French site
• custum color
Nice to have
• Wordpress design will be appréciate
• switch language english/french

```html
<!DOCTYPE html>
<html lang="en">
<head>
<meta charset="utf-8">
<title>Le Pont d'Oriole – Life Insurance Quotes</title>
<link href="https://fonts.googleapis.com/css2?family=Open+Sans:wght@400;600;700&display=swap" rel="stylesheet">
<style>
:root{
  --red:#d0121b;
  --red-dark:#a80d14;
  --orange:#d9a040;
  --green:#6cc45a;
  --cyan:#3ebfe0;
  --blue:#1b63a8;
  --blue-light:#2d86d3;
  --text:#333;
  --muted:#666;
  --line:#e3e3e3;
  --footer:#3a3a3a;
  --footer-bar:#2b2b2b;
}
*{box-sizing:border-box;margin:0;padding:0}
html,body{width:1200px;height:2378px;overflow:hidden}
body{position:relative;font-family:"Open Sans",Arial,sans-serif;color:var(--text);background:#fff}
.abs{position:absolute}
.topline{left:0;top:0;width:1200px;height:3px;background:var(--red)}
.header{left:0;top:3px;width:1200px;height:95px;background:#fff}
.logo{left:90px;top:3px;width:172px;height:147px;background:#fff;border-radius:0 0 86px 86px;z-index:3;display:flex;align-items:center;justify-content:center;box-shadow:0 2px 4px rgba(0,0,0,.08)}
.logo-name{display:flex;align-items:center;gap:6px;font-size:14px;font-weight:700;color:var(--red)}
.logo-name i{width:12px;height:12px;background:var(--red);display:block}
.nav{top:44px;left:0;font-size:13px;color:#333}
.nav a{position:absolute;white-space:nowrap;color:#333;text-decoration:none}
.nav a.active{color:var(--red)}
.lang{left:992px;top:42px;display:flex;align-items:center;gap:10px;font-size:14px;font-weight:600;color:var(--blue)}
.hero{left:0;top:98px;width:1200px;height:468px;
  background:
    radial-gradient(ellipse 260px 240px at 150px 340px,rgba(196,214,232,.85),transparent 70%),
    radial-gradient(ellipse 170px 200px at 380px 380px,rgba(214,220,236,.8),transparent 70%),
    radial-gradient(ellipse 150px 190px at 530px 380px,rgba(238,160,180,.75),transparent 70%),
    radial-gradient(ellipse 200px 260px at 660px 300px,rgba(150,120,95,.7),transparent 70%),
    radial-gradient(ellipse 140px 140px at 130px 180px,rgba(226,180,150,.8),transparent 70%),
    radial-gradient(ellipse 120px 120px at 680px 200px,rgba(232,190,160,.8),transparent 70%),
    radial-gradient(ellipse 400px 200px at 900px 120px,rgba(235,240,200,.7),transparent 70%),
    radial-gradient(ellipse 500px 220px at 300px 40px,rgba(110,140,70,.9),transparent 70%),
    linear-gradient(180deg,#7a9848 0%,#a6b56a 40%,#7f9a4c 75%,#5b7a32 100%)}
.hero-shadow{left:0;top:566px;width:1200px;height:14px;background:linear-gradient(#d8d8d8,#fff)}
.tab{top:528px;width:151px;height:71px;border:3px solid #fff;border-radius:4px;box-shadow:0 2px 4px rgba(0,0,0,.3);color:#fff;text-align:center;font-weight:600;font-size:17px;padding-top:7px;line-height:24px}
.tab span{display:block;font-size:16px;font-weight:400;text-decoration:underline}
.tab.vie{left:98px;background:var(--red)}
.tab.salaire{left:262px;background:var(--orange)}
.tab.hypo{left:423px;background:var(--green)}
.tab.graves{left:588px;background:var(--cyan);font-size:15px}
.quote{left:783px;top:165px;width:317px;height:761px;background:#f6f6f6;box-shadow:0 0 6px rgba(0,0,0,.2);border-radius:4px;z-index:2}
.quote-head{height:46px;background:linear-gradient(var(--red),var(--red-dark));color:#fff;font-size:20px;font-weight:600;text-align:center;line-height:46px;border-radius:4px 4px 0 0}
.q-label{position:absolute;left:21px;color:var(--red);font-size:15px;font-weight:600}
.q-field{position:absolute;left:21px;width:275px;height:38px;background:#fff;border:1px solid #e4e4e4;font-size:12px;color:#999;padding-left:8px;line-height:36px}
.q-field .chev{position:absolute;right:12px;top:0}
.radios{position:absolute;right:10px;top:0;display:flex;gap:22px}
.radios b{display:inline-block;width:9px;height:9px;border:1px solid #888;border-radius:50%;margin-right:7px;vertical-align:-1px;font-weight:400}
.radios b.on{background:radial-gradient(#555 40%,#fff 45%)}
.q-check{position:absolute;left:21px;font-size:12px;color:#333;display:flex;gap:14px;line-height:22px}
.q-check .box{width:18px;height:18px;border:1px solid #bbb;background:#fff;flex:none;margin-top:2px}
.captcha{position:absolute;left:109px;top:672px;width:187px;height:33px;background:#fff;border:1px solid #e4e4e4;font-style:italic;font-weight:700;color:var(--red-dark);font-size:17px;padding-left:14px;line-height:31px}
.send{position:absolute;left:0;bottom:0;width:317px;height:38px;background:linear-gradient(var(--red),var(--red-dark));color:#fff;font-size:17px;text-align:center;line-height:38px;border-radius:0 0 4px 4px}
.intro-title{left:98px;top:646px;font-size:25px;font-weight:600;color:var(--blue)}
.intro-sub{left:98px;top:688px;font-size:18px;color:#444}
.intro-text{left:98px;top:733px;width:660px;font-size:11.8px;line-height:26px;color:#444}
.btn-red{left:98px;top:889px;width:137px;height:37px;background:var(--red);color:#fff;font-size:13px;font-weight:600;border-radius:3px;text-align:center;line-height:37px}
.rule{left:98px;top:966px;width:1002px;height:2px;background:var(--blue)}
.blog-title{left:98px;top:1000px;font-size:26px;font-weight:600;color:var(--blue)}
.card{top:1073px;width:312px}
.card .img{width:312px;height:179px;border:2px solid #ddd}
.card .date{position:absolute;left:2px;top:2px;width:81px;height:55px;background:var(--blue);color:#fff;font-size:15px;line-height:20px;padding:7px 0 0 12px}
.card h3{margin-top:16px;font-size:15px;font-weight:400;color:#333;padding-left:1px;letter-spacing:.3px}
.card .d{margin-top:10px;font-size:12px;color:var(--blue);padding-left:3px}
.card p{margin-top:8px;font-size:12px;line-height:20px;color:#555;padding-left:3px;width:300px}
.card .more{text-align:right;font-size:12px;color:var(--blue);margin-top:12px;padding-right:20px}
.benefits{left:0;top:1477px;width:1200px;height:395px;background:linear-gradient(135deg,#3a93de,#0d63b8)}
.benefits-photo{left:0;top:1477px;width:634px;height:395px}
.ben-title{left:639px;top:1513px;font-size:24px;font-weight:600;color:#fff}
.ben-list{left:642px;top:1576px;width:480px;list-style:none;font-size:12.2px;color:#fff;line-height:22px}
.ben-list li{position:absolute;left:0;width:480px;padding-left:24px}
.ben-list li::before{content:"";position:absolute;left:0;top:8px;width:7px;height:7px;border-radius:50%;background:#fff}
.btn-outline{left:642px;top:1797px;width:119px;height:38px;border:2px solid #fff;border-radius:3px;color:#fff;font-size:15px;font-weight:600;text-align:center;line-height:34px}
.partner{top:1927px;width:236px;height:81px;border:2px solid #e6e6e6;border-radius:3px;display:flex;align-items:center;justify-content:center;gap:8px;font-size:20px;font-weight:600}
.partner i{width:16px;height:16px;display:block}
.footer{left:0;top:2057px;width:1200px;height:249px;background:var(--footer)}
.f-col{top:2094px;color:#fff;font-size:12px}
.f-col h4{font-size:15px;font-weight:600;margin-bottom:16px}
.f-col ul{list-style:none}
.f-col li{height:27.7px;padding-left:18px;position:relative}
.f-col li::before{content:"»";position:absolute;left:0;top:-2px;font-weight:700}
.f-about p{width:200px;line-height:21px;text-align:justify}
.f-contact .row{display:flex;gap:16px;margin-bottom:18px;line-height:20px}
.f-contact svg{flex:none;margin-top:2px}
.social{display:flex;gap:12px;margin-top:14px}
.social svg{display:block}
.bottom{left:0;top:2306px;width:1200px;height:72px;background:var(--footer-bar);color:#fff;font-size:12px;text-align:center;line-height:72px}
</style>
</head>
<body>
<div class="abs topline"></div>
<header class="abs header"></header>
<div class="abs logo"><div class="logo-name"><i></i>lepontdoriole.ca</div></div>
<nav class="abs nav">
  <a class="active" style="left:388px">Home</a>
  <a style="left:488px">Products</a>
  <a style="left:604px">Submission</a>
  <a style="left:737px">Who we are</a>
  <a style="left:870px">Contact us</a>
</nav>
<div class="abs lang">
  <svg width="32" height="18" viewBox="0 0 32 18"><rect width="32" height="18" fill="#1f3d8a"/><path d="M0 0L32 18M32 0L0 18" stroke="#fff" stroke-width="4"/><path d="M0 0L32 18M32 0L0 18" stroke="#c8102e" stroke-width="1.5"/><path d="M16 0V18M0 9H32" stroke="#fff" stroke-width="6"/><path d="M16 0V18M0 9H32" stroke="#c8102e" stroke-width="3"/></svg>
  <span>English</span>
  <svg width="8" height="5" viewBox="0 0 8 5"><path d="M0 0H8L4 5Z" fill="#999"/></svg>
</div>

<div class="abs hero" role="img" aria-label="Smiling family of four lying on the grass in a sunny park"></div>
<svg class="abs" style="left:1140px;top:320px" width="12" height="20" viewBox="0 0 12 20"><path d="M2 2L10 10L2 18" stroke="#fff" stroke-width="2" fill="none" opacity=".8"/></svg>
<div class="abs hero-shadow"></div>
<div class="abs tab vie">Assurance Vie<span>Bidding</span></div>
<div class="abs tab salaire">Salaire<span>Bidding</span></div>
<div class="abs tab hypo">Hypothecaire<span>Bidding</span></div>
<div class="abs tab graves">Maladies Graves<span>Bidding</span></div>

<form class="abs quote">
  <div class="quote-head">Quote Request</div>
  <div class="q-label" style="top:62px">Product</div>
  <div class="q-field" style="top:98px">Types Of Insurance<svg class="chev" width="10" height="36" viewBox="0 0 10 36"><path d="M1 16L5 20L9 16" stroke="#888" fill="none"/></svg></div>
  <div class="q-label" style="top:172px">Applicant</div>
  <div class="q-field" style="top:209px">Full Name</div>
  <div class="q-field" style="top:253px">Cities</div>
  <div class="q-field" style="top:298px">Email</div>
  <div class="q-field" style="top:342px">Telephone</div>
  <div class="q-field" style="top:387px">Age</div>
  <div class="q-field" style="top:431px">Gender<div class="radios"><span><b></b>Male</span><span><b class="on"></b>Female</span></div></div>
  <div class="q-label" style="top:514px">Co - Applicant</div>
  <div class="q-check" style="top:555px"><span class="box"></span>Add a Co-Applicant</div>
  <div class="q-check" style="top:590px;width:270px;font-size:11.5px"><svg width="18" height="20" viewBox="0 0 18 20" style="flex:none;margin-top:2px"><path d="M2 10L7 16L16 2" stroke="#1b63a8" stroke-width="2.5" fill="none"/></svg>I HAVE READ AND ACCEPT THE USE AND PRIVACY POLICY OF **</div>
  <div class="q-label" style="top:675px">Captcha</div>
  <div class="captcha">.oraled</div>
  <div class="send">Click To Send</div>
</form>

<h1 class="abs intro-title">Online Life Insurance Submission</h1>
<p class="abs intro-sub">Find The Best Insurance At The Best Price</p>
<p class="abs intro-text">Whether you are looking for life insurance, mortgage insurance or else you certainly want to pay the most advanta-geous price. Navigating among the many offers in the field of insurance can be a real headache. But thanks to the intervention of Financial Security Advisors of Pont Doriole .ca, will save you hours of fruitless search, and in addition, you will find an insurance policy that suits you, at a price that fully meets the constraints on your financial situation, whatever it is. We use an innovative, simple and effective</p>
<div class="abs btn-red">Read More Info</div>

<div class="abs rule"></div>
<h2 class="abs blog-title">Our Blog Posts</h2>

<article class="abs card" style="left:97px">
  <div class="img" role="img" aria-label="Young family standing in front of a modern house" style="background:radial-gradient(ellipse 60px 70px at 70px 120px,rgba(230,235,245,.9),transparent 70%),radial-gradient(ellipse 55px 90px at 140px 110px,rgba(70,110,170,.6),transparent 70%),radial-gradient(ellipse 70px 90px at 210px 90px,rgba(230,232,238,.9),transparent 70%),radial-gradient(ellipse 80px 40px at 260px 160px,rgba(90,140,60,.8),transparent 70%),linear-gradient(180deg,#a9c4dc 0%,#e8ecef 45%,#d9d8d2 70%,#7ea05e 100%)"></div>
  <div class="date">APR 7<br>2016</div>
  <h3>SUAS POSSIM NUSQUAM</h3>
  <div class="d">Apr 7 , 2016</div>
  <p>Odio vivendum mediocrem cum et, lobortis partien-do repudiandae id pro, mel amet semper sanctus in. Alterum ocurreret sea ex.</p>
  <div class="more">[ Read more ]</div>
</article>
<article class="abs card" style="left:439px">
  <div class="img" role="img" aria-label="Smiling senior man with his family blurred in the background" style="background:radial-gradient(ellipse 90px 70px at 90px 150px,rgba(110,160,215,.9),transparent 70%),radial-gradient(ellipse 50px 50px at 90px 60px,rgba(225,185,160,.8),transparent 70%),radial-gradient(ellipse 30px 60px at 240px 120px,rgba(210,60,60,.6),transparent 70%),radial-gradient(ellipse 30px 50px at 180px 120px,rgba(120,140,170,.5),transparent 70%),linear-gradient(180deg,#f0f1f2,#dcdfe2)"></div>
  <div class="date">APR 7<br>2016</div>
  <h3>CU PRI ELITR VITAE</h3>
  <div class="d">Apr 7 , 2016</div>
  <p>Odio vivendum mediocrem cum et, lobortis partien-do repudiandae id pro, mel amet semper sanctus in. Alterum ocurreret sea ex.</p>
  <div class="more">[Read more ]</div>
</article>
<article class="abs card" style="left:783px">
  <div class="img" role="img" aria-label="Senior couple reviewing documents together" style="background:radial-gradient(ellipse 70px 80px at 110px 130px,rgba(245,240,232,.95),transparent 70%),radial-gradient(ellipse 80px 90px at 240px 140px,rgba(120,165,215,.85),transparent 70%),radial-gradient(ellipse 40px 40px at 110px 60px,rgba(228,195,175,.8),transparent 70%),radial-gradient(ellipse 40px 40px at 230px 50px,rgba(220,180,160,.8),transparent 70%),linear-gradient(180deg,#e4e8ea,#f3f1ec)"></div>
  <div class="date">APR 7<br>2016</div>
  <h3>LABORES LIBERAVISSE QUI</h3>
  <div class="d">Apr 7 , 2016</div>
  <p>Odio vivendum mediocrem cum et, lobortis partien-do repudiandae id pro, mel amet semper sanctus in. Alterum ocurreret sea ex.</p>
  <div class="more">[ Read more ]</div>
</article>

<section class="abs benefits"></section>
<svg class="abs benefits-photo" width="634" height="395" viewBox="0 0 634 395" role="img" aria-label="Family lying on green grass in front of a house under a blue sky with clouds">
  <defs>
    <linearGradient id="sky" x1="0" y1="0" x2="0" y2="1"><stop offset="0" stop-color="#3f8fd8"/><stop offset=".5" stop-color="#a9cdee"/><stop offset=".68" stop-color="#86b450"/><stop offset="1" stop-color="#3f7d1e"/></linearGradient>
    <radialGradient id="cloud"><stop offset="0" stop-color="#fff" stop-opacity=".95"/><stop offset="1" stop-color="#fff" stop-opacity="0"/></radialGradient>
    <radialGradient id="warm"><stop offset="0" stop-color="#d9a27a" stop-opacity=".8"/><stop offset="1" stop-color="#d9a27a" stop-opacity="0"/></radialGradient>
    <radialGradient id="stone"><stop offset="0" stop-color="#9a948a" stop-opacity=".85"/><stop offset="1" stop-color="#9a948a" stop-opacity="0"/></radialGradient>
    <clipPath id="cut"><path d="M0 0H634L499 395H0Z"/></clipPath>
  </defs>
  <g clip-path="url(#cut)">
    <rect width="634" height="395" fill="url(#sky)"/>
    <ellipse cx="150" cy="70" rx="190" ry="60" fill="url(#cloud)"/>
    <ellipse cx="420" cy="110" rx="170" ry="55" fill="url(#cloud)"/>
    <ellipse cx="300" cy="30" rx="120" ry="35" fill="url(#cloud)" opacity=".7"/>
    <ellipse cx="440" cy="220" rx="90" ry="60" fill="url(#stone)"/>
    <ellipse cx="200" cy="270" rx="220" ry="80" fill="url(#warm)"/>
  </g>
</svg>
<h2 class="abs ben-title">Benefits And Features</h2>
<ul class="abs ben-list">
  <li style="top:0">Son coût est fixe durant toute la durée du contrat et peut être payé en totalité en quelques années (ex. : en 10 ou 20 ans);</li>
  <li style="top:61px">Cette assurance peut être contractée seule ou combinée avec d'autres types de protections d'assurance de personnes;</li>
  <li style="top:123px">Elle offre une protection pour la vie;</li>
  <li style="top:163px">Vous pouvez y ajouter des protections complémentaires telles que :</li>
</ul>
<div class="abs btn-outline">Read More</div>

<div class="abs partner" style="left:98px;color:#5a9a3c"><i style="background:#6cb33f;border-radius:50%"></i>Verdant Power</div>
<div class="abs partner" style="left:353px;color:#222"><i style="background:#d0121b"></i>SAFEGRID</div>
<div class="abs partner" style="left:609px;color:#333"><i style="background:#1b63a8;border-radius:50%"></i>Kova Capital</div>
<div class="abs partner" style="left:864px;color:#c8102e">Northwind Theme</div>

<footer class="abs footer"></footer>
<div class="abs f-col f-about" style="left:98px">
  <h4>ABOUT</h4>
  <p>Duo ne vero debitis admodum, ea dictas oporteat nam. Nec ad fugit graece facilis, vix ea malorum nominati rationibus, nam equidem sententiae ei.</p>
  <p style="margin-top:10px">[ Read More ]</p>
</div>
<div class="abs f-col" style="left:341px">
  <h4>MENUS</h4>
  <ul><li>Home</li><li>About us</li><li>Our services</li><li>Blog</li><li>Contact us</li></ul>
</div>
<div class="abs f-col" style="left:482px">
  <h4>QUICK LINKS</h4>
  <ul><li>Site map</li><li>Terms and Conditions</li><li>Disclaimer</li><li>Privacy Policy</li><li>Contact us</li></ul>
</div>
<div class="abs f-col f-contact" style="left:680px;width:230px">
  <h4>CONTACT US</h4>
  <div class="row"><svg width="16" height="14" viewBox="0 0 16 14"><path d="M8 0L16 7H13V14H9V9H7V14H3V7H0Z" fill="#fff"/></svg><span>2280 Rue des Érables | Laval QC H7T 1A2</span></div>
  <div class="row"><svg width="16" height="16" viewBox="0 0 16 16"><rect x="4" y="0" width="8" height="16" rx="1.5" fill="#fff"/><rect x="5.5" y="2" width="5" height="10" fill="#3a3a3a"/></svg><span>Call Us : (450)555-0182</span></div>
  <div class="row"><svg width="16" height="12" viewBox="0 0 16 12"><rect x="1" y="1" width="14" height="10" fill="none" stroke="#fff" stroke-width="1.5"/><path d="M1 1L8 7L15 1" fill="none" stroke="#fff" stroke-width="1.5"/></svg><span>info@lepontdoriole.ca</span></div>
</div>
<div class="abs f-col" style="left:921px">
  <h4>CONNECT US WITH</h4>
  <div class="social">
    <svg width="36" height="36" viewBox="0 0 36 36" role="img" aria-label="Share link"><circle cx="18" cy="18" r="16.5" fill="none" stroke="#fff" stroke-width="2"/><circle cx="12" cy="18" r="2.5" fill="#fff"/><circle cx="24" cy="12" r="2.5" fill="#fff"/><circle cx="24" cy="24" r="2.5" fill="#fff"/><path d="M12 18L24 12M12 18L24 24" stroke="#fff" stroke-width="1.5"/></svg>
    <svg width="36" height="36" viewBox="0 0 36 36" role="img" aria-label="Email"><circle cx="18" cy="18" r="16.5" fill="none" stroke="#fff" stroke-width="2"/><rect x="10" y="12" width="16" height="12" fill="none" stroke="#fff" stroke-width="1.6"/><path d="M10 12L18 19L26 12" fill="none" stroke="#fff" stroke-width="1.6"/></svg>
    <svg width="36" height="36" viewBox="0 0 36 36" role="img" aria-label="Phone"><circle cx="18" cy="18" r="16.5" fill="none" stroke="#fff" stroke-width="2"/><rect x="13" y="9" width="10" height="18" rx="2" fill="#fff"/><rect x="14.8" y="11.5" width="6.4" height="11" fill="#3a3a3a"/></svg>
    <svg width="36" height="36" viewBox="0 0 36 36" role="img" aria-label="Location"><circle cx="18" cy="18" r="16.5" fill="none" stroke="#fff" stroke-width="2"/><path d="M18 27C18 27 11.5 19.5 11.5 15.5A6.5 6.5 0 0 1 24.5 15.5C24.5 19.5 18 27 18 27Z" fill="#fff"/><circle cx="18" cy="15.5" r="2.4" fill="#3a3a3a"/></svg>
  </div>
</div>
<div class="abs bottom">© &nbsp;Lepontdoriole 2016 . All Rights Reserved</div>
</body>
</html>
```